Torvel’s letterhead for local government

I require a letterhead for quarterly communications with constituents. The colours I have used in the past are navy & green (together) so I’m happy to use similar colours for this. Please refer to business card as an example.
The letter must make reference to the position I hold which is as per below
“Clr Torvel Quennisbury OAM”
And the tag line I have used in the past is “Torvel on the Terrace”. Although I’m not sure if this would be used in a letterhead or not. Happy for this to be provided as an option.
I would like a photo in the letterhead as I believe face recognition is key as an elected member.

Target Market(s)

Political interests

Industry/Entity Type

Government Office

Font styles to use
Sans Serif

Requirements
Must have
• Politically professional. I have been an elected member for 2 years so it is expected that the letterhead conveys that. The colours of the business card is to be used.
Nice to have
• Background of photos to be manipulated or changed to make me stand out, if possible?
Should not have
• Looked like it’s cropped or undertaken by an amateur designer.

```html
<!DOCTYPE html>
<html lang="en">
<head>
<meta charset="utf-8">
<title>Torvel Quennisbury – Letterhead</title>
<link href="https://fonts.googleapis.com/css2?family=Arimo:wght@400;700&family=Open+Sans:wght@400;600&display=swap" rel="stylesheet">
<style>
  :root {
    --navy: #2a5d91;
    --navy-text: #1f4f86;
    --green: #3fb664;
    --green-text: #27ad4f;
    --ink: #444444;
    --ink-dark: #333333;
    --paper: #ffffff;
    --photo-light: #e4e4e4;
    --photo-dark: #a9adb3;
  }
  * { margin: 0; padding: 0; box-sizing: border-box; }
  html, body { width: 1040px; height: 1200px; overflow: hidden; background: var(--paper); }
  .letterhead {
    position: relative; width: 1040px; height: 1200px; background: var(--paper);
    font-family: "Open Sans", Arial, sans-serif; color: var(--ink);
  }
  .swoosh { position: absolute; left: 0; top: 0; width: 1040px; height: 1200px; }
  .portrait {
    position: absolute; left: 93px; top: 37px; width: 212px; height: 191px; border-radius: 5px;
    background: radial-gradient(ellipse at 50% 45%, var(--photo-dark) 0%, #c3c6ca 40%, var(--photo-light) 75%);
  }
  .identity { position: absolute; left: 340px; top: 98px; font-family: "Arimo", Arial, sans-serif; }
  .identity-name { font-size: 31px; line-height: 38px; font-weight: 700; color: var(--navy-text); letter-spacing: 0.2px; }
  .identity-role { margin-top: 9px; font-size: 23px; line-height: 26px; color: var(--green-text); }
  .meta { position: absolute; left: 98px; font-size: 16.5px; line-height: 18.5px; }
  .meta-date { top: 255px; }
  .meta-recipient { top: 290px; }
  .salutation { position: absolute; left: 98px; top: 394px; font-size: 16.5px; }
  .body-copy { position: absolute; left: 98px; top: 441px; width: 842px; font-size: 16.3px; line-height: 27px; text-align: justify; }
  .body-copy p + p { margin-top: 27px; }
  .closing { position: absolute; left: 98px; top: 852px; font-size: 16.5px; }
  .signatory { position: absolute; left: 98px; top: 929px; }
  .signatory-name { font-size: 19px; font-weight: 600; color: var(--ink-dark); }
  .signatory-title { margin-top: 3px; font-size: 16.5px; }
  .contact {
    position: absolute; right: 108px; top: 1111px; list-style: none;
    font-family: "Arimo", Arial, sans-serif; font-size: 20px; line-height: 22px; color: #fff;
  }
  .contact li { display: flex; justify-content: flex-end; align-items: center; gap: 8px; }
  .contact svg { width: 20px; height: 20px; }
</style>
</head>
<body>
<main class="letterhead">
  <svg class="swoosh" viewBox="0 0 1040 1200" aria-hidden="true">
    <polygon fill="var(--green)" points="400,0 525,0 995,80 985,81"/>
    <polygon fill="var(--navy)" points="545,0 1040,0 1040,80"/>
    <polygon fill="var(--green)" points="0,1138 817,1091 0,1186"/>
    <polygon fill="var(--navy)" points="0,1194 1040,1067 1040,1200 0,1200"/>
  </svg>

  <div class="portrait" role="img" aria-label="Portrait photo of Clr Torvel Quennisbury in a dark suit and tie"></div>

  <header class="identity">
    <h1 class="identity-name">Clr Torvel Quennisbury OAM</h1>
    <p class="identity-role">Candidate for Area Councillor<br>City of Marrowfield</p>
  </header>

  <p class="meta meta-date">Issuing Date: May 5, 2018</p>
  <p class="meta meta-recipient">Name Of Employee Mr. XYZABC<br>Address of Employee<br>Address Line 2 etc..</p>

  <p class="salutation">Dear Mr.XYZABC</p>

  <section class="body-copy">
    <p>Lorem Ipsum has been the industry's standard dummy text ever since the 1500s, when an unknown printer took a galley of type and scrambled it to make a type specimen book. It has survived not only five centuries, but also the leap into electronic typesetting, remaining essentially unchanged. It was popularised in the 1960s with the release of Pressmark sheets containing Lorem Ipsum passages, and more recently with desktop publishing software like Quillform PageDesk including versions of Lorem Ipsum.</p>
    <p>Lorem Ipsum is simply dummy text of the printing and typesetting industry. Lorem Ipsum has been the industry's standard dummy text ever since the 1500s, when an unknown printer took a galley of type and scrambled it to make a type specimen book.</p>
    <p>It has survived not only five centuries, but also the leap into electronic typesetting, remaining essentially unchanged. It was popularised in the 1960s with the release of Pressmark sheets containing Lorem IpsumIpsum passages.</p>
  </section>

  <p class="closing">Yours Sincerely</p>

  <div class="signatory">
    <p class="signatory-name">Merrick Dalloway</p>
    <p class="signatory-title">Managing Director</p>
  </div>

  <ul class="contact">
    <li>045-210 387 614
      <svg viewBox="0 0 20 20"><circle cx="10" cy="10" r="8.5" fill="none" stroke="#fff" stroke-width="1.5"/><path d="M7 5.5c-.8.5-1.3 1.3-1 2.5.6 2.5 3 5 5.5 5.8 1.2.3 2-.2 2.5-1l-1.6-1.4-1.2.8c-1.2-.6-2.2-1.6-2.8-2.8l.8-1.2z" fill="#fff"/></svg>
    </li>
    <li>info@quennisbury-office.com
      <svg viewBox="0 0 20 20"><circle cx="10" cy="10" r="8.5" fill="none" stroke="#fff" stroke-width="1.5"/><rect x="5.5" y="7" width="9" height="6.5" rx="1" fill="#fff"/><path d="M5.8 7.4 10 10.6l4.2-3.2" fill="none" stroke="var(--navy)" stroke-width="1"/></svg>
    </li>
    <li>www.torvelquennisbury.com
      <svg viewBox="0 0 20 20"><circle cx="10" cy="10" r="8.5" fill="none" stroke="#fff" stroke-width="1.5"/><circle cx="10" cy="10" r="4.6" fill="none" stroke="#fff" stroke-width="1.2"/><ellipse cx="10" cy="10" rx="2" ry="4.6" fill="none" stroke="#fff" stroke-width="1"/><path d="M5.4 10h9.2" stroke="#fff" stroke-width="1"/></svg>
    </li>
  </ul>
</main>
</body>
</html>
```